Basic business card

use my newly created logo - and the phrases (Lower Cost of Test & Accelarated New Product Introduction) - and my new email domain / ID - use at conferences / tradeshows

Industry/Entity Type

semiconductor

Contact Information for Business Card

Daniel K Forde, Owner, communicate via Logo - Lower COT - Cost of Test, Accelerated NPI - New Product Introduction, phone +1 555 613 0946, Chandler, Arizona, USA, daniel.forde@qal-vub.com

Font styles to use
Sans Serif

Requirements
Nice to have
• re-use my logo created via Pixel Harbor last August (#7315926)

```html
<!DOCTYPE html>
<html lang="en">
<head>
<meta charset="utf-8">
<title>QAL-VUB Business Card</title>
<link rel="stylesheet" href="https://fonts.googleapis.com/css2?family=Open+Sans:wght@400;600;700&display=swap">
<style>
  :root {
    --backdrop: #222222;
    --card-dark: #232428;
    --card-light: #f4f4f4;
    --accent-green: #6db33f;
    --slate: #4a5468;
    --steel: #8c95a8;
    --text-light: #e9eaec;
  }
  * { margin: 0; padding: 0; box-sizing: border-box; }
  html, body {
    width: 1200px; height: 779px; overflow: hidden;
    background: var(--backdrop);
    font-family: "Open Sans", sans-serif;
  }
  .canvas { position: relative; width: 1200px; height: 779px; }
  .card {
    position: absolute; top: 241px;
    width: 520px; height: 297px;
    background: var(--card-dark);
    overflow: hidden;
    box-shadow: 0 10px 30px rgba(0,0,0,0.45);
  }
  .card--front { left: 50px; }
  .card--back { left: 630px; display: flex; align-items: center; justify-content: center; }

  .front-curve { position: absolute; inset: 0; }

  .brand-mark {
    position: absolute; top: 22px; left: 170px;
    font-size: 30px; font-weight: 400; letter-spacing: 2px;
    color: var(--slate);
  }

  .identity {
    position: absolute; top: 86px; left: 30px;
    padding-left: 12px;
    border-left: 6px solid var(--accent-green);
  }
  .identity__name { font-size: 22px; font-weight: 700; color: #ffffff; line-height: 1.15; }
  .identity__first { color: var(--accent-green); }
  .identity__title { font-size: 13px; color: var(--text-light); }

  .address {
    position: absolute; top: 150px; left: 48px;
    font-size: 12px; line-height: 1.45; color: var(--text-light);
  }
  .contact-list {
    position: absolute; top: 195px; left: 30px;
    list-style: none; font-size: 12px; line-height: 1.6; color: var(--text-light);
  }
  .contact-list li { display: flex; align-items: center; gap: 7px; }
  .contact-list svg { width: 11px; height: 11px; fill: var(--accent-green); }

  .brand-panel {
    position: absolute; left: 385px; top: 196px;
    display: flex; align-items: center; gap: 8px;
    font-size: 24px; font-weight: 600; color: var(--slate);
  }
  .brand-panel__square, .brand-back__square {
    width: 14px; height: 14px; background: var(--accent-green);
  }

  .brand-back {
    display: flex; align-items: center; gap: 12px;
    font-size: 46px; font-weight: 400; letter-spacing: 3px; color: var(--steel);
  }
  .brand-back__square { width: 20px; height: 20px; }
</style>
</head>
<body>
<main class="canvas">
  <section class="card card--front">
    <svg class="front-curve" viewBox="0 0 520 297" width="520" height="297" aria-hidden="true">
      <path d="M318 297 C340 170 420 85 520 60 L520 297 Z" fill="var(--accent-green)"/>
      <path d="M332 297 C352 182 428 100 520 76 L520 297 Z" fill="var(--card-light)"/>
    </svg>

    <div class="brand-mark">QAL-VUB</div>

    <div class="identity">
      <p class="identity__name"><span class="identity__first">Lena</span> Marvik</p>
      <p class="identity__title">Managing Director</p>
    </div>

    <p class="address">418 Orchard Ridge Rd. Suite 12<br>Brookvale, TX 75990</p>

    <ul class="contact-list">
      <li>
        <svg viewBox="0 0 24 24"><path d="M6.6 10.8a15.2 15.2 0 0 0 6.6 6.6l2.2-2.2c.3-.3.7-.4 1-.2 1.1.4 2.3.6 3.6.6.6 0 1 .4 1 1V20c0 .6-.4 1-1 1A17 17 0 0 1 3 4c0-.6.4-1 1-1h3.5c.6 0 1 .4 1 1 0 1.3.2 2.5.6 3.6.1.3 0 .7-.2 1z"/></svg>
        (555) 274-8013
      </li>
      <li>
        <svg viewBox="0 0 24 24"><path d="M2 5h20v14H2z M4 7v.5l8 5 8-5V7l-8 5z"/></svg>
        hello@qal-vub.com
      </li>
      <li>
        <svg viewBox="0 0 24 24"><circle cx="12" cy="12" r="10"/></svg>
        www.qal-vub.com
      </li>
    </ul>

    <div class="brand-panel">
      <span class="brand-panel__square"></span>QAL-VUB
    </div>
  </section>

  <section class="card card--back">
    <div class="brand-back">
      <span class="brand-back__square"></span>QAL-VUB
    </div>
  </section>
</main>
</body>
</html>
```